Business Card Design Project

Business and Appointment Card for Medical Practice. On back of card we would like to have: blank line for patient name, Mon-Fri each with a check box next to the day, blank line for appointment date, blank line for appointment time, with option to circle am or pm.

Target Market(s)

Professional Business Associates, as well as function as patient appointment cards (on back side of card)

Industry/Entity Type

Business

Colors

Designer to choose colors to be used in the design.

```html
<!DOCTYPE html>
<html lang="en">
<head>
<meta charset="utf-8">
<title>Birch Lane Medical Associates – Business &amp; Appointment Card</title>
<link rel="stylesheet" href="https://fonts.googleapis.com/css2?family=Open+Sans:wght@400;600&display=swap">
<style>
  :root {
    --page-bg: #e4e4e4;
    --card-bg: #ffffff;
    --brand-red: #8c1c1f;
    --brand-green: #1e6a38;
    --rule-green: #2f7a45;
    --faint-ring: #ecebe8;
    --shadow: rgba(0,0,0,0.18);
  }
  * { box-sizing: border-box; margin: 0; padding: 0; }
  html, body { width: 1200px; height: 900px; overflow: hidden; }
  body {
    background: var(--page-bg);
    font-family: "Open Sans", sans-serif;
    position: relative;
  }
  .card {
    position: absolute;
    top: 300px;
    width: 520px;
    height: 300px;
    background: var(--card-bg);
    border-radius: 24px;
    box-shadow: 0 10px 28px var(--shadow);
    overflow: hidden;
  }
  .card--front { left: 50px; }
  .card--back { left: 630px; }

  /* Front */
  .brand {
    position: absolute;
    top: 62px;
    left: 0; right: 0;
    display: flex;
    flex-direction: column;
    align-items: center;
    gap: 14px;
  }
  .brand__dot {
    width: 56px; height: 56px;
    border-radius: 50%;
    border: 3px solid var(--brand-green);
  }
  .brand__name {
    color: var(--brand-red);
    font-weight: 600;
    font-size: 25px;
    letter-spacing: 0.5px;
    text-align: center;
    line-height: 1.15;
  }
  .brand-band {
    position: absolute;
    top: 196px;
    left: 0; right: 0;
    height: 8px;
    background: var(--brand-red);
  }
  .person {
    position: absolute;
    top: 228px;
    right: 310px;
    text-align: right;
  }
  .person__name { color: var(--brand-red); font-size: 16px; }
  .person__role { color: var(--brand-green); font-size: 11px; margin-top: 2px; }
  .contact-divider {
    position: absolute;
    top: 220px;
    left: 224px;
    width: 2px;
    height: 62px;
    background: var(--rule-green);
  }
  .contact {
    position: absolute;
    top: 218px;
    left: 240px;
    list-style: none;
    color: var(--brand-green);
    font-size: 14px;
    line-height: 17px;
  }
  .contact li { display: flex; align-items: center; gap: 6px; }
  .contact svg { width: 12px; height: 12px; fill: var(--brand-red); flex: none; }

  /* Back */
  .decor-ring {
    position: absolute;
    left: 100px;
    top: 14px;
    width: 320px;
    height: 320px;
    border-radius: 50%;
    border: 6px solid var(--faint-ring);
  }
  .appointment {
    position: absolute;
    inset: 0;
    padding: 64px 26px 0 34px;
    color: var(--brand-green);
  }
  .appointment__title {
    color: var(--brand-red);
    font-size: 16px;
    font-weight: 400;
    text-align: center;
    margin-bottom: 12px;
  }
  .field {
    display: flex;
    align-items: flex-end;
    height: 42px;
    font-size: 17px;
  }
  .field__label { width: 62px; display: flex; justify-content: space-between; padding-right: 4px; }
  .field__line {
    border-bottom: 2px dotted var(--brand-green);
    margin-bottom: 6px;
    height: 1px;
  }
  .field__line--full { flex: 1; }
  .field__line--date { width: 180px; }
  .field__line--time { width: 180px; }
  .weekdays { display: flex; gap: 6px; margin-left: 8px; font-size: 11px; align-items: flex-end; margin-bottom: 2px; }
  .weekday { display: flex; align-items: flex-end; gap: 2px; }
  .weekday__box { width: 14px; height: 14px; border: 1.3px solid var(--brand-green); display: inline-block; }
  .ampm { font-size: 12px; margin-left: 8px; margin-bottom: 3px; }
</style>
</head>
<body>

<section class="card card--front" aria-label="Business card front">
  <div class="brand">
    <span class="brand__dot"></span>
    <div class="brand__name">Birch Lane<br>Medical Associates</div>
  </div>
  <div class="brand-band"></div>

  <div class="person">
    <div class="person__name">Daniel Reyes</div>
    <div class="person__role">Manager</div>
  </div>
  <div class="contact-divider"></div>
  <ul class="contact">
    <li><svg viewBox="0 0 24 24"><path d="M6.6 10.8a15 15 0 0 0 6.6 6.6l2.2-2.2c.3-.3.7-.4 1-.2 1.1.4 2.3.6 3.6.6.6 0 1 .4 1 1V20c0 .6-.4 1-1 1A17 17 0 0 1 3 4c0-.6.4-1 1-1h3.5c.6 0 1 .4 1 1 0 1.3.2 2.5.6 3.6.1.3 0 .7-.2 1z"/></svg>555-210-4830</li>
    <li><svg viewBox="0 0 24 24"><path d="M12 2a10 10 0 1 0 0 20 10 10 0 0 0 0-20zm6.9 6h-3a15 15 0 0 0-1.3-3.9A8 8 0 0 1 18.9 8zM12 4c.8 1.2 1.5 2.5 1.9 4h-3.8c.4-1.5 1.1-2.8 1.9-4zM4.3 14a8 8 0 0 1 0-4h3.4a16 16 0 0 0 0 4zm.8 2h3a15 15 0 0 0 1.3 3.9A8 8 0 0 1 5.1 16zm3-8h-3a8 8 0 0 1 4.3-3.9C8.8 5.3 8.4 6.6 8.1 8zM12 20c-.8-1.2-1.5-2.5-1.9-4h3.8c-.4 1.5-1.1 2.8-1.9 4zm2.3-6H9.7a14 14 0 0 1 0-4h4.6a14 14 0 0 1 0 4zm.3 5.9c.6-1.2 1-2.5 1.3-3.9h3a8 8 0 0 1-4.3 3.9zm1.7-5.9a16 16 0 0 0 0-4h3.4a8 8 0 0 1 0 4z"/></svg>www.birchlanemed.com</li>
    <li><svg viewBox="0 0 24 24"><path d="M2 5h20v14H2zm2 2v.5l8 5 8-5V7zm0 2.8V17h16V9.8l-8 5z"/></svg>info@birchlanemed.com</li>
    <li><svg viewBox="0 0 24 24"><path d="M12 3 2 12h3v8h5v-5h4v5h5v-8h3z"/></svg>142 Harbor Lane Easton</li>
  </ul>
</section>

<section class="card card--back" aria-label="Appointment card back">
  <div class="decor-ring"></div>
  <div class="appointment">
    <h2 class="appointment__title">Appointment</h2>
    <div class="field">
      <span class="field__label"><span>Name</span><span>:</span></span>
      <span class="field__line field__line--full"></span>
    </div>
    <div class="field">
      <span class="field__label"><span>Date</span><span>:</span></span>
      <span class="field__line field__line--date"></span>
      <span class="weekdays">
        <span class="weekday">Mon<i class="weekday__box"></i></span>
        <span class="weekday">Tue<i class="weekday__box"></i></span>
        <span class="weekday">Wed<i class="weekday__box"></i></span>
        <span class="weekday">Thu<i class="weekday__box"></i></span>
        <span class="weekday">Fri<i class="weekday__box"></i></span>
      </span>
    </div>
    <div class="field">
      <span class="field__label"><span>Time</span><span>:</span></span>
      <span class="field__line field__line--time"></span>
      <span class="ampm">am / pm</span>
    </div>
  </div>
</section>

</body>
</html>
```